verdant terraces simple classy business card design

my name is colin barrow and I run a gardening business aimed at high class verdant terraces. the business name is verdant terraces and our logo was designed on pixel harbour .My clientel are anything from residential homes to businesses. I take pride in my work and know that I offer a service like no other in my area.
The business card will be used to represent my business and I want it to be not only rememberable, but simplistic and modern. Eye catching too. Of course I would like it relatable to gardening and appealing to the correct clientel - those being garden enthusiasts, prestigious homes and businesses that are after top of the line gardening services like no other on the market.
I am not a typical lawn mowing business so I don't want a typical card design that represents that. The gardens I work with are generally million dollar properties with owners who are very garden proud looking for upkeep and guidance from me along with sometimes whole new garden designs. I want the business cards to show to my clients that I take pride, as they do, in their garden. And I want them to know from my card that I am a professional, qualified horticulturist offering them a top of the line service for life. I want them to refer my business on. I want them to look at my business card and see class and professionalism in a modern unique bold way.
The card should be simple with the possibility of the logo on the front being embossed/debossed and my details on the back the card should have a organic garden feel it's very important to me that it is absolutely perfect
I am also very open to ideas and suggestions so look forward to seeing the designs. the business logo has been supplied with this project and I want the card to be double sided

Contact info is
Colin Barrow - Managing Director / Horticulturist
Phone : 0481 526 704
Email: colinbarrow@verdantterraces.example.au

Target Market(s)

high class gardens residential and commercial

Industry/Entity Type

Gardener

Contact Information for Business Card

Contact info is
Phone : 0481 526 704

PLEASE MAKE CARD DOUBLE SIDED

Requirements
Must have
• organic simple classy modern feel
• must flow with the current logo that has been supplied with this project
• Double sided
• Must explain in a simple way that I deal with high end gardens and I'm a qualified horticulturist
Nice to have
• embossed debossed logo
Should not have
• shouldn't be to busy or cheap looking

```html
<!DOCTYPE html>
<html lang="en">
<head>
<meta charset="utf-8">
<title>Verdant Terraces – Business Card</title>
<link rel="stylesheet" href="https://fonts.googleapis.com/css2?family=Open+Sans:wght@400;600;700&display=swap">
<style>
  :root {
    --backdrop: #eeece8;
    --card-green: #5fa352;
    --card-green-deep: #4b8c40;
    --emblem-green: #7dbb6f;
    --card-text: #f3f8f1;
  }
  * { margin: 0; padding: 0; box-sizing: border-box; }
  html, body {
    width: 1200px; height: 900px; overflow: hidden;
    background: var(--backdrop);
    font-family: "Open Sans", Arial, sans-serif;
  }
  .canvas { position: relative; width: 1200px; height: 900px; }
  .card {
    position: absolute;
    background: var(--card-green);
    color: var(--card-text);
  }
  .card--front { left: 238px; top: 60px; width: 555px; height: 343px; }
  .card--back  { left: 459px; top: 518px; width: 560px; height: 343px; }

  .brand-mark {
    position: absolute; left: 50%; top: 28px;
    width: 92px; height: 92px; margin-left: -46px;
    border-radius: 50%;
    border: 2px solid var(--card-green-deep);
  }
  .brand-name {
    position: absolute; left: 0; right: 0; top: 132px;
    text-align: center;
    font-weight: 600; font-size: 33px; letter-spacing: 4px;
    color: var(--card-green-deep);
  }

  .person {
    position: absolute; right: 312px; top: 216px; text-align: right;
  }
  .person__name { font-weight: 700; font-size: 17px; line-height: 22px; }
  .person__role { font-size: 13px; line-height: 18px; }

  .contacts {
    position: absolute; left: 265px; top: 216px; list-style: none;
  }
  .contacts__item {
    display: flex; align-items: center; gap: 8px;
    font-size: 13px; line-height: 20px;
    white-space: nowrap;
  }
  .contacts__icon { width: 11px; height: 11px; fill: var(--card-text); flex: none; }

  .credentials {
    position: absolute; left: 0; right: 0; top: 292px;
    text-align: center; font-size: 13px; line-height: 20px;
  }

  .emblem {
    position: absolute; left: 50%; top: 50%;
    width: 270px; height: 270px; margin: -135px 0 0 -135px;
    border-radius: 50%;
    background: var(--emblem-green);
    border: 4px solid var(--card-green-deep);
    display: flex; align-items: center; justify-content: center;
  }
  .emblem__name {
    font-weight: 600; font-size: 20px; letter-spacing: 3px;
    color: var(--card-green-deep); text-align: center; line-height: 28px;
  }
</style>
</head>
<body>
<main class="canvas">
  <section class="card card--front" aria-label="Business card front">
    <div class="brand-mark"></div>
    <div class="brand-name">VERDANT TERRACES</div>

    <div class="person">
      <div class="person__name">Colin Barrow</div>
      <div class="person__role">Managing Director</div>
      <div class="person__role">Horticulturist</div>
    </div>

    <ul class="contacts">
      <li class="contacts__item">
        <svg class="contacts__icon" viewBox="0 0 12 12"><path d="M2.5 0.5 L4.5 0.5 L5.3 3 L3.9 4 C4.6 5.7 6.3 7.4 8 8.1 L9 6.7 L11.5 7.5 L11.5 9.5 C11.5 10.6 10.6 11.5 9.5 11.5 C4.6 11.2 0.8 7.4 0.5 2.5 C0.5 1.4 1.4 0.5 2.5 0.5 Z"/></svg>
        <span>0481 526 704</span>
      </li>
      <li class="contacts__item">
        <svg class="contacts__icon" viewBox="0 0 12 12"><path d="M1 2.5 H11 V9.5 H1 Z M1.6 3 L6 6.4 L10.4 3" stroke="#5fa352" stroke-width="0.9"/></svg>
        <span>colinbarrow@verdantterraces.example.au</span>
      </li>
      <li class="contacts__item">
        <svg class="contacts__icon" viewBox="0 0 12 12"><circle cx="6" cy="6" r="5.5"/><path d="M0.5 6 H11.5 M6 0.5 C3.5 3 3.5 9 6 11.5 M6 0.5 C8.5 3 8.5 9 6 11.5" stroke="#5fa352" stroke-width="0.8" fill="none"/></svg>
        <span>www.verdantterraces.example.au</span>
      </li>
    </ul>

    <div class="credentials">Qualified Horticulturist · High-End Residential &amp; Commercial Gardens</div>
  </section>

  <section class="card card--back" aria-label="Business card back">
    <div class="emblem">
      <div class="emblem__name">VERDANT<br>TERRACES</div>
    </div>
  </section>
</main>
</body>
</html>
```